Security Guard company needs new procedure template to wow potential clients in tender submissions

We need an update to our procedure template that will look very professional and modern. We have many procedures so this template must be editable so the content can be adjusted by us depending on the procedure.
A smart and modern professional front page with editable title etc.
A professional and modern page template for the body of the procedure.

We wish to copy and paste our word document onto this template and be able to use it easily.

I have attached our logo and example of a procedure we have.

Font styles to use
Sans Serif

Requirements
Must have
• Ability for me to edit text and add new sections to the document.
Use as a template for multiple procedures.

```html
<!DOCTYPE html>
<html lang="en">
<head>
<meta charset="utf-8">
<title>Kestrel Guard Services – Procedure Template</title>
<link href="https://fonts.googleapis.com/css2?family=Poppins:wght@400;500;600;700;900&display=swap" rel="stylesheet">
<style>
  :root{
    --bg:#89d4d9;
    --red:#d21f2c;
    --red-dark:#b81a26;
    --ink:#1f1f1f;
    --ink-soft:#333;
    --grey:#e8e4e3;
    --dark:#2b2b2b;
    --paper:#ffffff;
    --rule:#9a9a9a;
  }
  *{margin:0;padding:0;box-sizing:border-box}
  html,body{width:1200px;height:949px;overflow:hidden}
  body{background:var(--bg);font-family:"Poppins",sans-serif;color:var(--ink);position:relative}

  .page{position:absolute;top:51px;height:731px;background:var(--paper);overflow:hidden}
  .page--cover{left:83px;width:515px}
  .page--body{left:598px;width:510px}

  /* cover / index page */
  .spine-edge{position:absolute;left:0;top:0;width:10px;height:100%;background:var(--grey)}
  .cover-title{position:absolute;left:28px;top:4px;font-weight:900;font-size:84px;line-height:1;color:var(--red);letter-spacing:-1px}
  .cover-subtitle{position:absolute;left:29px;top:75px;font-weight:700;font-size:17px;color:var(--ink)}
  .brand-band{position:absolute;right:0;top:22px;width:160px;height:84px;background:var(--grey)}
  .brand-stripes{position:absolute;left:316px;top:22px}
  .brand-name{font-weight:700;color:var(--red);white-space:nowrap;line-height:1}
  .brand-band .brand-name{position:absolute;left:16px;top:30px;font-size:15px}
  .brand-band .brand-mark{position:absolute;left:16px;top:52px;width:10px;height:10px;background:var(--red)}

  .toc{position:absolute;left:50px;top:143px;width:392px;list-style:none}
  .toc li{display:flex;align-items:flex-end;height:30.8px;font-weight:600;font-size:11.5px;letter-spacing:.4px}
  .toc .leader{flex:1;border-bottom:1px dashed var(--rule);margin:0 6px 4px}
  .toc .num{width:14px;text-align:left;font-size:10px}

  /* body page */
  .doc-brand{position:absolute;left:7px;top:48px;display:flex;align-items:center;gap:4px}
  .doc-brand .brand-mark{width:8px;height:8px;background:var(--red)}
  .doc-brand .brand-name{font-size:9px}
  .doc-header{position:absolute;left:110px;top:0}
  .doc-header-title{position:absolute;left:132px;top:24px;color:#fff;font-size:9.5px;font-weight:500;transform:rotate(-2deg);transform-origin:left top;white-space:nowrap}
  .page-tab{position:absolute;right:0;top:0;width:64px;height:49px;background:var(--dark);color:#fff;font-weight:700;text-align:center;line-height:1;padding-top:12px}
  .page-tab span{display:block;font-size:10px}
  .page-tab strong{display:block;font-size:14px}

  .doc-content{position:absolute;left:21px;top:93px;width:470px;font-size:7.6px;line-height:1.4;color:var(--ink-soft)}
  .doc-content h2{color:var(--red);font-size:10.5px;font-weight:700;margin:12px 0 6px -9px}
  .doc-content h2:first-child{margin-top:0}
  .doc-content h3{font-size:7.6px;font-weight:700;color:var(--ink);margin:12px 0 4px}
  .doc-content p{margin-bottom:6px}
  .doc-content ul{list-style:none;margin-bottom:4px}
  .doc-content li{position:relative;padding-left:9px;margin-bottom:6px}
  .doc-content li::before{content:"";position:absolute;left:-3px;top:3px;width:4px;height:4px;background:var(--red);transform:rotate(45deg)}

  .doc-footer{position:absolute;left:0;right:0;top:666px;border-top:1.5px solid var(--red);text-align:center;font-size:7.6px;padding-top:12px;line-height:1.6}
  .doc-footer b{color:var(--red);font-weight:500}

  .caption{position:absolute;top:818px;font-weight:600;font-size:27px;letter-spacing:2px;color:#fff}
  .caption--cover{left:210px}
  .caption--body{left:811px}
</style>
</head>
<body>

<section class="page page--cover">
  <div class="spine-edge"></div>
  <h1 class="cover-title">INDEX</h1>
  <p class="cover-subtitle">Table of contents</p>

  <svg class="brand-stripes" width="60" height="84" viewBox="0 0 60 84" aria-hidden="true">
    <polygon points="13,0 20,0 7,84 0,84" fill="#d21f2c"/>
    <polygon points="29,0 49,0 36,84 16,84" fill="#d21f2c"/>
  </svg>
  <div class="brand-band">
    <span class="brand-name">KESTREL GUARD</span>
    <span class="brand-mark"></span>
  </div>

  <ol class="toc">
    <li>1.Purpose<span class="leader"></span><span class="num">3</span></li>
    <li>2.Scope<span class="leader"></span><span class="num">3</span></li>
    <li>3.Responsibilities<span class="leader"></span><span class="num">3</span></li>
    <li>4.HSE Management System<span class="leader"></span><span class="num">5</span></li>
    <li>5.KGSL HSE Core Values<span class="leader"></span><span class="num">6</span></li>
    <li>6.KGSL HSE Policy Statement<span class="leader"></span><span class="num">6</span></li>
    <li>7.KGSL HSE Policy Commitments<span class="leader"></span><span class="num">6</span></li>
    <li>8.Accidents<span class="leader"></span><span class="num">7</span></li>
    <li>9.Consultation<span class="leader"></span><span class="num">8</span></li>
    <li>10.Fire<span class="leader"></span><span class="num">8</span></li>
    <li>11.Personal Protective Equipment<span class="leader"></span><span class="num">9</span></li>
    <li>12.Housekeeping<span class="leader"></span><span class="num">9</span></li>
    <li>13.Waste Disposal<span class="leader"></span><span class="num">10</span></li>
    <li>14.Monitoring<span class="leader"></span><span class="num">10</span></li>
    <li>15.Training<span class="leader"></span><span class="num">10</span></li>
    <li>16.Fit to Work Policy<span class="leader"></span><span class="num">11</span></li>
    <li>17.Drug and Alcohol Policy<span class="leader"></span><span class="num">11</span></li>
  </ol>
</section>

<section class="page page--body">
  <div class="doc-brand">
    <span class="brand-mark"></span>
    <span class="brand-name">KESTREL GUARD</span>
  </div>

  <svg class="doc-header" width="340" height="70" viewBox="0 0 340 70" aria-hidden="true">
    <polygon points="0,0 334,0 334,40 18,70" fill="#2b2b2b"/>
    <polygon points="4,0 334,0 334,37 22,66" fill="#d21f2c"/>
  </svg>
  <p class="doc-header-title">KGSL- HSE001 – Health, Safety and Environment Policy - REV 02</p>
  <div class="page-tab"><span>PG</span><strong>01</strong></div>

  <div class="doc-content">
    <h2>1.Purpose</h2>
    <p>The purpose of this Health and Safety (HSE) Plan is to:</p>
    <ul>
      <li>Provide a statement of the Kestrel Guard Services Limited (KGSL) aspired level of Health and Safety performance and how this will be reached over the current year.</li>
      <li>Document the Health and Safety objectives, targets, key performance indicators, improvement plans, audits and communication initiatives.</li>
    </ul>

    <h2>2.Scope</h2>
    <p>This annual Health and Safety plan is issued as a part of the KGSL Health and Safety Management System. This plan covers all activities undertaken by KGSL.</p>

    <h2>2.Responsibilities</h2>
    <h3>Owner</h3>
    <p>The Owner of this HSE Plan is the Director, who has the collective responsibility for:</p>
    <ul>
      <li>Approving and endorsing the HSE Plan.</li>
      <li>Ensuring that resources are available to execute the HSE Plan</li>
      <li>Monitoring implementation of the HSE Plan and initiating corrective action where necessary.</li>
    </ul>

    <h3>Custodian</h3>
    <p>The Custodian of the plan is the Operations Manager who has the responsibility for:</p>
    <ul>
      <li>Developing the plan.</li>
      <li>Reporting status of implementation of the HSE Plan and the need for adjustments</li>
      <li>Ensuring that employees are competent and adequately trained to discharge their defined HSE responsibilities;</li>
      <li>Ensuring employees under their control discharge their defined HSE responsibilities;</li>
      <li>Ensuring that they, and all employees under their direction, adhere to the HSE policy and procedure</li>
    </ul>

    <h3>Implementer</h3>
    <p>The Implementers of the plan are the Supervisors who have the responsibility for:</p>
    <ul>
      <li>Carrying out pre contract site health, safety and welfare assessments;</li>
      <li>Ensuring risk assessments, welfare arrangements and emergency procedures are defined in assignment instructions;</li>
      <li>Ensuring employees are provided with information, training and supervision as necessary to work safely;</li>
      <li>Undertaking site inspections to ensure assignment instructions are being adhered to;</li>
      <li>Consulting with Security Officers on safety matters;</li>
      <li>Undertaking accident investigations of all incidents with the potential for serious injury;</li>
    </ul>
  </div>

  <footer class="doc-footer">
    42 Lakeview Road, Eastfield, Northbridge 400512<br>
    <b>Ph:</b> +91 90000 12345, <b>Email:</b> info@kestrelguard.example, <b>Website:</b> www.kestrelguard.example
  </footer>
</section>

<p class="caption caption--cover">Cover Page</p>
<p class="caption caption--body">Index Page</p>

</body>
</html>
```